Vietnam Motorcycle Trip TRAVEL GUIDE!! Book Cover!

I need an adventurous book cover for a book called "THROTTLE MERIDIAN: A Wanderer's Manual for Crossing the Breadth of Vietnam". I would like people to look at the cover and think adventure and Vietnam. I want it to appeal to backpackers and people who have not travelled to Vietnam. A motorbike riding along a road in Vietnam would be ideal with some landscapes to suggest we are definitely in Vietnam. The rear cover could perhaps be one of Vietnam's tropical beaches or something else that says "this place is a paradise". It could also be something else that is quinessentially Vietnamese.

The book will be A5 Dimensions. And it will also need a printable A5 interior cover too. The interior covers can just be images. No text needed. These interior images can be motorcycle related or Vietnam related. Perhaps some images of Vietnam or some Pho or Banh Mi to give it a bit of flavour. Or a long open road with a motorbike on it.

Please leave space in the external rear, lower right hand corner for a barcode.

I've attached some images to gain inspiration from. And a sample chapter.

Colours I'd like to see on there - greens, camoflague perhaps, yellow, brown, blue.

Target Market(s)

Male backpackers aged 18-35 years old. New Zealand and Australian travellers.

Font styles to use
Serif
Sans Serif

Requirements
Must have
• Exterior and Interior covers.
Barcode space.
Title and subtitle.
Synopsis on rear cover.
Exciting title fonts - perhaps Brushstroke or something equally exciting and rugged
Nice to have
• Colours I'd like to see on there - greens, camoflague perhaps, yellow, brown, blue.

A motorbike riding on the open road of Vietnam.

Rice paddies, beaches, Korvan Conflict stuff perhaps.

A New Zealand Flag
A Vietnam Flag
Should not have
• Scenery from countries outside Southeast Asia

```html
<!DOCTYPE html>
<html lang="en">
<head>
<meta charset="utf-8">
<title>Throttle Meridian – Cover Layout</title>
<link rel="stylesheet" href="https://fonts.googleapis.com/css2?family=Permanent+Marker&family=Rock+Salt&family=Oswald:wght@500;600;700&family=Lato:wght@400;700&display=block">
<style>
  :root{
    --board:#6f6f6f;
    --yellow:#f4d81c;
    --yellow-deep:#d8b80c;
    --blue:#1466c4;
    --ink:#111111;
    --spine:#111417;
    --brush:#6b6b4e;
    --leaf:#3f7d2c;
    --leaf-dark:#1f4a22;
    --road:#7d8580;
    --white:#ffffff;
    --brush-font:"Permanent Marker","Rock Salt",fantasy;
  }
  *{margin:0;padding:0;box-sizing:border-box}
  html,body{width:888px;height:1200px;overflow:hidden;background:var(--board)}
  .board{position:relative;width:888px;height:1200px}

  .panel{position:relative;width:388px;height:554px;overflow:hidden;
    background:radial-gradient(ellipse at 50% 40%,var(--yellow) 0%,var(--yellow) 55%,var(--yellow-deep) 100%)}
  .front{width:388px}

  .wrap-cover{position:absolute;left:36px;top:39px;width:815px;height:554px;display:flex;box-shadow:4px 5px 8px rgba(0,0,0,.45)}
  .board > .single{position:absolute;top:623px;transform:scale(.966);transform-origin:top left;box-shadow:4px 5px 8px rgba(0,0,0,.45)}
  .board > .back-single{left:36px}
  .board > .front-single{left:478px}

  /* back */
  .back-headline{position:absolute;left:23px;top:20px;width:350px;font-family:"Lato",sans-serif;font-weight:400;font-size:20px;line-height:24px;color:var(--ink);letter-spacing:-.3px}
  .back-headline b{color:var(--blue);font-weight:700}
  .synopsis{position:absolute;left:23px;width:345px;font-family:"Lato",sans-serif;font-size:7.3px;line-height:9.6px;color:var(--ink)}
  .synopsis.intro{top:76px}
  .synopsis.author-note{top:125px}
  .reveals-label{position:absolute;left:23px;top:154px;font-family:"Lato",sans-serif;font-weight:400;font-size:9.3px;color:var(--blue);letter-spacing:-.1px}
  .reveals{position:absolute;left:23px;top:171px;width:345px;list-style:none;font-family:"Lato",sans-serif;font-size:9px;line-height:10px;color:var(--ink)}
  .reveals li{position:relative;padding-left:15px;margin-bottom:8.5px}
  .reveals li::before{content:"";position:absolute;left:3px;top:3px;width:4.5px;height:4.5px;border-radius:50%;background:var(--ink)}
  .closing{position:absolute;left:23px;top:315px;width:345px;font-family:"Lato",sans-serif;font-size:7.3px;line-height:9.8px;color:var(--ink)}
  .back-photo{position:absolute;left:0;top:365px;width:100%;height:189px;
    background:
      radial-gradient(ellipse 60% 40% at 70% 70%,rgba(40,50,45,.55) 0%,rgba(40,50,45,0) 100%),
      linear-gradient(170deg,rgba(244,216,28,0) 0%,#8aa430 12%,var(--leaf) 24%,#b9b9a8 36%,#8a918c 50%,var(--road) 70%,#4f5f58 100%)}
  .paradise{position:absolute;left:22px;top:342px;font-family:var(--brush-font);font-size:23px;line-height:1;color:var(--ink);letter-spacing:.3px;white-space:nowrap;transform:skewX(-6deg)}
  .flags{position:absolute;left:23px;top:501px;display:flex;gap:2px}
  .flag{width:32px;height:21px}
  .flag.red{background:#e0401c}
  .flag.navy{background:#1c2f79}
  .site{position:absolute;left:23px;top:527px;font-family:"Lato",sans-serif;font-size:7px;letter-spacing:.6px;color:var(--white)}
  .guide-tag{position:absolute;left:313px;top:456px;font-family:"Lato",sans-serif;font-size:6px;color:rgba(255,255,255,.7);letter-spacing:.3px}
  .barcode-space{position:absolute;left:248px;top:464px;width:115px;height:69px;background:var(--white);display:flex;align-items:center;justify-content:center;font-family:"Lato",sans-serif;font-size:5px;letter-spacing:2px;color:#444}

  /* spine */
  .spine{position:relative;width:39px;height:554px;background:var(--spine)}
  .spine-title{position:absolute;left:50%;top:20px;transform:translateX(-50%);writing-mode:vertical-rl;font-family:var(--brush-font);font-size:15px;color:var(--white);letter-spacing:2px;white-space:nowrap}
  .spine-sub{position:absolute;left:50%;top:308px;transform:translateX(-50%);writing-mode:vertical-rl;font-family:"Oswald",sans-serif;font-weight:600;font-size:7px;color:var(--white);letter-spacing:1px;white-space:nowrap}

  /* front */
  .title{position:absolute;left:20px;width:350px;font-family:var(--brush-font);font-weight:400;text-align:center;white-space:nowrap;line-height:1}
  .title.line-one{top:20px;font-size:46px;color:var(--blue);letter-spacing:2px;transform:skewX(-8deg)}
  .title.line-two{top:76px;font-size:46px;color:var(--ink);letter-spacing:6px;transform:skewX(-8deg)}
  .subtitle-band{position:absolute;left:28px;top:138px;width:340px;height:108px}
  .subtitle{position:absolute;left:52px;top:160px;width:290px;transform:rotate(-8deg);font-family:"Oswald",sans-serif;font-weight:600;font-style:italic;font-size:16.5px;line-height:19px;color:var(--white);text-align:center;text-transform:uppercase;letter-spacing:.4px}
  .front-photo{position:absolute;left:0;top:250px;width:100%;height:304px;
    background:
      radial-gradient(ellipse 42% 50% at 38% 45%,rgba(40,100,40,.95) 0%,rgba(40,100,40,0) 100%),
      radial-gradient(ellipse 30% 28% at 80% 55%,rgba(30,90,50,.9) 0%,rgba(30,90,50,0) 100%),
      radial-gradient(ellipse 22% 30% at 55% 92%,rgba(150,155,145,.9) 0%,rgba(150,155,145,0) 100%),
      linear-gradient(180deg,rgba(244,216,28,0) 0%,#c9d45a 16%,#9fbf6a 34%,#5f9a45 62%,#4e8a34 78%,#5d7a3f 100%)}
  .author{position:absolute;left:0;top:511px;width:100%;text-align:center;font-family:"Oswald",sans-serif;font-weight:700;font-size:22px;letter-spacing:5px;color:var(--yellow)}
</style>
</head>
<body>
<main class="board">

  <section class="wrap-cover" aria-label="Full wrap cover">
    <article class="panel back">
      <h2 class="back-headline"><b>TRAVEL LIKE A PRO</b> IN A COUNTRY WHERE BRIBING COPS IS <b>NORMAL!</b></h2>
      <p class="synopsis intro">Everyone knows someone who’s ridden the length of Vietnam. What if you could do the same? For us Kiwis and Australians, it’s difficult finding decent material about motorcycling in Vietnam. With so much conflicting information online and uncertainty around costs, it’s no wonder people keep putting off this 1600 km road trip.</p>
      <p class="synopsis author-note">Callum Ashvale has been there and done it. In the flesh. And whether your goal is riding from Saigon to Hanoi or between beach towns, this guide is your bulletproof vest.</p>
      <h3 class="reveals-label">THIS STEP-BY-STEP WANDERER’S MANUAL REVEALS:</h3>
      <ul class="reveals">
        <li>How to plan your own road trip before leaving home</li>
        <li>Where and how to buy/rent a bike</li>
        <li>What types of licences and insurance you’ll need</li>
        <li>How to finish your trip alive without being run over by a pig truck</li>
        <li>How to avoid getting shaken down by dodgy cops</li>
        <li>Itemized expense reports, showing this journey is possible for as little as NZ$90 per day and even as low as $50.</li>
        <li>A day-by-day riding itinerary</li>
      </ul>
      <p class="closing">Let’s face it. None of us are getting any younger. Your own Vietnam road trip awaits. And with all the information you need in one lightweight book, what’s stopping you?</p>
      <div class="back-photo" role="img" aria-label="Photo of two riders on a scooter on a curving mountain road, one waving"></div>
      <p class="paradise">THIS PLACE IS A PARADISE!</p>
      <div class="flags">
        <div class="flag red" role="img" aria-label="Vietnam flag"></div>
        <div class="flag navy" role="img" aria-label="New Zealand flag"></div>
      </div>
      <p class="site">meridianride.net</p>
      <p class="guide-tag">TRAVEL GUIDE</p>
      <div class="barcode-space">BARCODE AREA</div>
    </article>

    <aside class="spine">
      <span class="spine-title">THROTTLE MERIDIAN</span>
      <span class="spine-sub">A WANDERER’S MANUAL FOR CROSSING THE BREADTH OF VIETNAM</span>
    </aside>

    <article class="panel front">
      <h1 class="title line-one">THROTTLE</h1>
      <h1 class="title line-two">MERIDIAN</h1>
      <svg class="subtitle-band" viewBox="0 0 340 108" aria-hidden="true">
        <path d="M22 62 C90 40 200 18 300 6 L338 4 L316 14 L336 20 L306 30 L330 36 L312 48 L326 56 L286 72 C200 86 110 98 44 104 L6 102 L26 94 L2 88 L30 80 L10 72 Z" fill="var(--brush)"/>
      </svg>
      <p class="subtitle">A Wanderer’s Manual<br>for Crossing the<br>Breadth of Vietnam</p>
      <div class="front-photo" role="img" aria-label="Photo of a limestone karst mountain above a country road with two motorbikes riding toward the viewer"></div>
      <p class="author">CALLUM ASHVALE</p>
    </article>
  </section>

  <article class="single back-single panel back">
    <h2 class="back-headline"><b>TRAVEL LIKE A PRO</b> IN A COUNTRY WHERE BRIBING COPS IS <b>NORMAL!</b></h2>
    <p class="synopsis intro">Everyone knows someone who’s ridden the length of Vietnam. What if you could do the same? For us Kiwis and Australians, it’s difficult finding decent material about motorcycling in Vietnam. With so much conflicting information online and uncertainty around costs, it’s no wonder people keep putting off this 1600 km road trip.</p>
    <p class="synopsis author-note">Callum Ashvale has been there and done it. In the flesh. And whether your goal is riding from Saigon to Hanoi or between beach towns, this guide is your bulletproof vest.</p>
    <h3 class="reveals-label">THIS STEP-BY-STEP WANDERER’S MANUAL REVEALS:</h3>
    <ul class="reveals">
      <li>How to plan your own road trip before leaving home</li>
      <li>Where and how to buy/rent a bike</li>
      <li>What types of licences and insurance you’ll need</li>
      <li>How to finish your trip alive without being run over by a pig truck</li>
      <li>How to avoid getting shaken down by dodgy cops</li>
      <li>Itemized expense reports, showing this journey is possible for as little as NZ$90 per day and even as low as $50.</li>
      <li>A day-by-day riding itinerary</li>
    </ul>
    <p class="closing">Let’s face it. None of us are getting any younger. Your own Vietnam road trip awaits. And with all the information you need in one lightweight book, what’s stopping you?</p>
    <div class="back-photo" role="img" aria-label="Photo of two riders on a scooter on a curving mountain road, one waving"></div>
    <p class="paradise">THIS PLACE IS A PARADISE!</p>
    <div class="flags">
      <div class="flag red" role="img" aria-label="Vietnam flag"></div>
      <div class="flag navy" role="img" aria-label="New Zealand flag"></div>
    </div>
    <p class="site">meridianride.net</p>
  </article>

  <article class="single front-single panel front">
    <h1 class="title line-one">THROTTLE</h1>
    <h1 class="title line-two">MERIDIAN</h1>
    <svg class="subtitle-band" viewBox="0 0 340 108" aria-hidden="true">
      <path d="M22 62 C90 40 200 18 300 6 L338 4 L316 14 L336 20 L306 30 L330 36 L312 48 L326 56 L286 72 C200 86 110 98 44 104 L6 102 L26 94 L2 88 L30 80 L10 72 Z" fill="var(--brush)"/>
    </svg>
    <p class="subtitle">A Wanderer’s Manual<br>for Crossing the<br>Breadth of Vietnam</p>
    <div class="front-photo" role="img" aria-label="Photo of a limestone karst mountain above a country road with two motorbikes riding toward the viewer"></div>
    <p class="author">CALLUM ASHVALE</p>
  </article>

</main>
</body>
</html>
```